Design a web site for my business - Brightline Coatings Co.

We are a family business that handles design, fabrication and installation of powder coated aluminum, stainless steel and glass products. Including handrails, privacy slat screens, electric gates and pool fencing. We are based in the Whitsundays in North Queensland and service an area from Airlie Beach to Townsville.

Target Market(s)

Domestic and commercial

Industry/Entity Type

fabrication - manufacturing

Coding

Coded - Design and coding required

Number of Pages Required

5+ page

Colors
0054AA
0677BA
7BADD7
CADEEF
E8F1F8

Requirements
Must have
• photo galleries, contact page, one page for privacy screens, balustrades, glass fencing, stainless steel handrail, powder coated aluminium handrails and pool fencing

```html
<!DOCTYPE html>
<html lang="en">
<head>
<meta charset="utf-8">
<title>Brightline Coatings Co — Aluminium &amp; Glass</title>
<link href="https://fonts.googleapis.com/css2?family=Bebas+Neue&family=Poppins:wght@400;500;600;700&display=swap" rel="stylesheet">
<style>
:root{
  --navy:#0054AA;
  --navy-deep:#003d7e;
  --accent:#0677BA;
  --sky:#7BADD7;
  --mist:#CADEEF;
  --ice:#E8F1F8;
  --ink:#1d2230;
  --muted:#4b5264;
  --white:#ffffff;
  --head:"Bebas Neue",sans-serif;
  --body:"Poppins",sans-serif;
}
*{margin:0;padding:0;box-sizing:border-box}
html,body{width:1200px;height:4914px;overflow:hidden}
body{position:relative;font-family:var(--body);color:var(--ink);background:var(--white)}
.abs{position:absolute}
.section{position:absolute;left:0;width:1200px;overflow:hidden}
.eyebrow{font-size:11px;font-weight:600;color:var(--accent);line-height:14px}
.h2{font-family:var(--head);font-weight:400;font-size:38px;line-height:1.02;color:var(--navy);letter-spacing:.3px}
.center{text-align:center;left:0;width:1200px}
.lead{font-size:11px;line-height:1.6;color:var(--muted)}
.btn{position:absolute;display:flex;align-items:center;justify-content:center;border-radius:20px;font-size:9.5px;font-weight:600}
.btn-main{background:var(--accent);color:#fff}
.btn-ghost{border:1.5px solid #fff;color:#fff}
.btn-outline{border:1.5px solid var(--accent);color:var(--accent);background:#fff}
.photo{position:absolute}

/* hero */
.hero{top:0;height:729px;background:linear-gradient(100deg,#1c2325 0%,#2b3632 35%,#3d6e6b 60%,#36a3b3 78%,#5bbfcf 100%)}
.hero-shade{position:absolute;inset:0;background:linear-gradient(90deg,rgba(10,14,20,.72) 0%,rgba(10,14,20,.35) 55%,rgba(0,0,0,0) 100%)}
.brand{position:absolute;left:151px;top:28px;color:#fff;font-family:var(--head);font-size:22px;line-height:.9}
.brand small{display:block;font-family:var(--body);font-size:9px;font-weight:700;letter-spacing:.3px;margin-top:3px}
.nav{position:absolute;left:428px;top:36px;display:flex;align-items:center;gap:19px;font-size:10px;color:#fff;font-weight:500}
.call{position:absolute;left:798px;top:22px;display:flex;align-items:center;gap:10px;color:#fff}
.call .ico{width:34px;height:34px;border-radius:50%;background:var(--accent);display:flex;align-items:center;justify-content:center}
.call b{font-size:11px;display:block;line-height:1.25}
.quote-top{left:1000px;top:27px;width:104px;height:30px;background:var(--navy);color:#fff}
.hero-eyebrow{color:var(--sky)}
.hero h1{position:absolute;left:151px;top:302px;font-family:var(--head);font-size:50px;line-height:.9;color:#fff;font-weight:400}
.hero .intro{position:absolute;left:151px;top:402px;width:460px;font-size:10.5px;line-height:1.55;color:#fff}
.stats{position:absolute;top:636px;left:151px;display:flex;color:#fff}
.stat{text-align:center}
.stat b{display:block;font-family:var(--head);font-size:26px;font-weight:400;line-height:1}
.stat span{font-size:10px}

/* about */
.about{top:729px;height:654px}
.about .text{position:absolute;left:636px;top:184px;width:420px}
.about .text p{font-size:10.5px;line-height:1.65;color:var(--muted);margin-top:14px}

/* services */
.services{top:1383px;height:649px;background:var(--ice)}
.cards{position:absolute;left:151px;top:197px;display:flex;gap:6px}
.card{width:221px;height:338px;background:#fff;box-shadow:0 6px 16px rgba(0,40,90,.1);position:relative}
.card .img{height:188px}
.card h3{font-family:var(--head);font-weight:400;font-size:17px;line-height:1;color:var(--navy);margin:16px 0 0 26px}
.card p{font-size:9.5px;line-height:1.55;color:var(--muted);margin:6px 22px 0 26px}
.card .go{position:absolute;left:26px;bottom:20px;width:26px;height:26px;background:var(--accent);display:flex;align-items:center;justify-content:center}

/* process */
.process{top:2032px;height:448px;background:linear-gradient(180deg,#0062b8 0%,var(--navy) 55%,var(--navy-deep) 100%)}
.step{position:absolute;top:190px;width:205px;color:#fff}
.step .num{font-family:var(--body);font-weight:400;font-size:60px;color:var(--sky);line-height:1;letter-spacing:-1px}
.step h3{font-family:var(--head);font-weight:400;font-size:17px;line-height:1;margin-top:18px}
.step p{font-size:9.5px;line-height:1.6;margin-top:6px;opacity:.92}
.arrow{position:absolute;top:212px}

/* projects */
.projects{top:2480px;height:935px}
.tile{position:absolute}
.tile-feature{position:absolute;background:var(--accent);color:#fff;text-align:center;display:flex;flex-direction:column;justify-content:center;padding:0 30px}
.tile-feature h3{font-family:var(--head);font-weight:400;font-size:19px;line-height:1}
.tile-feature p{font-size:10px;line-height:1.6;margin-top:8px}

/* area */
.area{top:3415px;height:468px}
.area .text{position:absolute;left:151px;top:112px;width:420px}
.area p{font-size:10.5px;line-height:1.6;color:var(--muted);margin-top:14px}

/* testimonials */
.reviews{top:3883px;height:425px}
.review{position:absolute;top:107px;width:294px;height:215px;border:1.5px solid var(--sky);background:linear-gradient(180deg,#ffffff 0%,var(--ice) 100%);padding:46px 32px 0}
.stars{color:var(--accent);font-size:12px;letter-spacing:1px}
.review p{font-size:10px;line-height:1.65;color:var(--muted);margin-top:8px}
.review .who{font-size:9.5px;color:var(--muted);margin-top:12px}
.review .who b{color:var(--ink)}
.dots{position:absolute;top:339px;left:584px;display:flex;gap:6px}
.dots i{width:5px;height:5px;border-radius:50%;background:var(--mist)}
.dots i.on{background:var(--accent)}

/* cta */
.cta{top:4308px;height:185px;background:linear-gradient(95deg,var(--navy-deep) 0%,var(--navy) 45%,var(--accent) 75%,var(--navy) 100%)}

/* footer */
.footer{top:4493px;height:421px;background:var(--navy);color:#fff}
.fcol{position:absolute;top:78px}
.fcol h4{font-family:var(--head);font-weight:400;font-size:17px;line-height:1;letter-spacing:.3px}
.fcol h4::after{content:"";display:block;width:20px;height:2px;background:var(--sky);margin-top:6px}
.fcol ul{list-style:none;margin-top:12px}
.fcol li{font-size:10.5px;line-height:22px;opacity:.9}
.contact-row{position:absolute;top:298px;display:flex;align-items:center;gap:14px}
.contact-row .ico{width:30px;height:30px;border-radius:50%;background:rgba(255,255,255,.12);display:flex;align-items:center;justify-content:center}
.contact-row b{display:block;font-size:10px;line-height:1.35}
.legal{position:absolute;top:380px;left:204px;width:816px;display:flex;justify-content:space-between;font-size:9.5px;opacity:.85}
.totop{position:absolute;left:1106px;top:386px;width:26px;height:26px;border-radius:50%;background:#fff;display:flex;align-items:center;justify-content:center}
</style>
</head>
<body>

<!-- HERO -->
<header class="section hero">
  <div class="photo" style="inset:0" role="img" aria-label="Modern house with glass balustrade deck overlooking an infinity pool and tropical islands"></div>
  <div class="hero-shade"></div>
  <div class="brand">BRIGHTLINE<small>COATINGS CO</small></div>
  <nav class="nav">
    <svg width="12" height="12" viewBox="0 0 12 12"><path d="M6 1 1 5.5h1.5V11h3V8h1v3h3V5.5H11z" fill="#7BADD7"/></svg>
    <span>Home</span><span>About</span><span>Services</span><span>Projects</span><span>Service Area</span><span>Contact</span>
  </nav>
  <div class="call">
    <span class="ico"><svg width="14" height="14" viewBox="0 0 24 24"><path d="M6.6 10.8a15 15 0 0 0 6.6 6.6l2.2-2.2c.3-.3.7-.4 1-.2 1.1.4 2.3.6 3.6.6.6 0 1 .4 1 1V20c0 .6-.4 1-1 1A17 17 0 0 1 3 4c0-.6.4-1 1-1h3.5c.6 0 1 .4 1 1 0 1.3.2 2.5.6 3.6.1.3 0 .7-.2 1z" fill="#fff"/></svg></span>
    <span><b>Call Us:</b><b>07 4900 1234</b></span>
  </div>
  <div class="btn quote-top">Get a Quote</div>

  <div class="eyebrow hero-eyebrow abs" style="left:151px;top:280px">Family Owned &amp; Operated — Whitsundays</div>
  <h1>CRAFTING EXCELLENCE IN<br>ALUMINIUM &amp; GLASS</h1>
  <p class="intro">Design, fabrication &amp; installation of powder coated aluminium, stainless steel &amp; glass products across the Whitsundays region — from Airlie Beach to Townsville.</p>
  <div class="btn btn-main" style="left:151px;top:451px;width:132px;height:31px">Request a Free Quote</div>
  <div class="btn btn-ghost" style="left:291px;top:451px;width:115px;height:31px">Our Services</div>

  <div class="stats">
    <div class="stat" style="width:95px"><b>15+</b><span>Years Experience</span></div>
    <div class="stat" style="width:105px;margin-left:62px"><b>500+</b><span>Projects Completed</span></div>
    <div class="stat" style="width:90px;margin-left:58px"><b>100%</b><span>Family Owned</span></div>
    <div class="stat" style="width:100px;margin-left:55px"><b>24/7</b><span>Customer Support</span></div>
  </div>
  <svg class="abs" style="left:0;top:0" width="1200" height="729"><polygon points="750,729 1068,729 1040,700 778,700" fill="#0054AA"/></svg>
</header>

<!-- ABOUT -->
<section class="section about">
  <svg class="abs" style="left:0;top:0" width="1200" height="654"><polygon points="140,556 320,556 292,584 140,584" fill="#0054AA"/></svg>
  <div class="photo" style="left:151px;top:80px;width:344px;height:432px;background:linear-gradient(135deg,#8a6a4a,#3b3029 55%,#6e7b86)" role="img" aria-label="Fabricator welding metal with sparks in the workshop"></div>
  <div class="photo" style="left:350px;top:256px;width:242px;height:300px;background:#fff;clip-path:polygon(0 0,100% 0,100% 82%,82% 100%,0 100%)"></div>
  <div class="photo" style="left:354px;top:260px;width:234px;height:292px;background:linear-gradient(180deg,#c9ccd0,#8f99a3 50%,#b7bcc2);clip-path:polygon(0 0,100% 0,100% 82%,82% 100%,0 100%)" role="img" aria-label="Warehouse stacked with aluminium extrusions"></div>
  <div class="text">
    <div class="eyebrow">About Our Business</div>
    <h2 class="h2" style="margin-top:8px;font-size:36px">A FAMILY TRADITION<br>OF QUALITY CRAFTSMANSHIP</h2>
    <p>We are a proud family-run business based in the heart of the Whitsundays, North Queensland. For over 15 years, we have been designing, fabricating and installing premium powder coated aluminium, stainless steel and glass products for homes and businesses throughout the region.</p>
    <p style="margin-top:8px">From concept to completion, our hands-on approach ensures every project meets the highest standards. We treat every job — big or small — with the same care and attention to detail that you'd expect from a family business.</p>
  </div>
  <div class="btn btn-outline" style="left:636px;top:432px;width:162px;height:30px">Get in touch with our family</div>
</section>

<!-- SERVICES -->
<section class="section services">
  <svg class="abs" style="left:0;top:0" width="1200" height="649"><polygon points="1200,-36 1200,340 1150,390 930,168" fill="#7BADD7"/></svg>
  <div class="eyebrow abs center" style="top:68px">What We Do</div>
  <h2 class="h2 abs center" style="top:88px">PREMIUM ALUMINIUM &amp; GLASS SOLUTIONS</h2>
  <p class="lead abs center" style="top:142px">From design to installation, we deliver complete solutions for residential and<br>commercial properties across the Whitsundays region.</p>
  <div class="cards">
    <article class="card">
      <div class="img" style="background:linear-gradient(160deg,#c7d0d6,#6d7a7f 60%,#4a5457)" role="img" aria-label="Stainless and glass handrail on a timber staircase"></div>
      <h3>HANDRAILS</h3>
      <p>Durable powder coated aluminium and stainless handrails for stairs, balconies and ramps.</p>
      <div class="go"><svg width="10" height="10" viewBox="0 0 10 10"><path d="M1 5h7M5 2l3 3-3 3" stroke="#fff" stroke-width="1.3" fill="none"/></svg></div>
    </article>
    <article class="card">
      <div class="img" style="background:linear-gradient(170deg,#9dc8a0,#3f6b3d 55%,#2a2f2b)" role="img" aria-label="Black aluminium slat gate surrounded by tropical garden"></div>
      <h3>PRIVACY SLAT SCREENS</h3>
      <p>Modern aluminium slat screens for patios, fences, carports and outdoor living areas.</p>
      <div class="go"><svg width="10" height="10" viewBox="0 0 10 10"><path d="M1 5h7M5 2l3 3-3 3" stroke="#fff" stroke-width="1.3" fill="none"/></svg></div>
    </article>
    <article class="card">
      <div class="img" style="background:linear-gradient(180deg,#c6d6de,#7d8c94 55%,#55606a)" role="img" aria-label="Grey electric sliding gate in front of a modern home"></div>
      <h3>ELECTRIC GATES</h3>
      <p>Secure automatic aluminium gates with smooth operation and smart access control.</p>
      <div class="go"><svg width="10" height="10" viewBox="0 0 10 10"><path d="M1 5h7M5 2l3 3-3 3" stroke="#fff" stroke-width="1.3" fill="none"/></svg></div>
    </article>
    <article class="card">
      <div class="img" style="background:linear-gradient(180deg,#7fb4d8,#4c8a5a 45%,#37b2d6 70%,#1c88c2)" role="img" aria-label="Frameless glass pool fence beside a resort pool"></div>
      <h3>POOL FENCING</h3>
      <p>Compliant frameless glass, semi-frameless and aluminium fencing for any pool area.</p>
      <div class="go"><svg width="10" height="10" viewBox="0 0 10 10"><path d="M1 5h7M5 2l3 3-3 3" stroke="#fff" stroke-width="1.3" fill="none"/></svg></div>
    </article>
  </div>
</section>

<!-- PROCESS -->
<section class="section process">
  <svg class="abs" style="left:0;top:0" width="1200" height="448"><polygon points="0,0 150,0 0,120" fill="#E8F1F8"/></svg>
  <div class="eyebrow abs center" style="top:70px;color:var(--sky)">How It Works</div>
  <h2 class="h2 abs center" style="top:90px;color:#fff">FROM FIRST CALL TO FINAL FIT</h2>
  <div class="step" style="left:175px"><div class="num">01</div><h3>CONSULT &amp; MEASURE</h3><p>We visit your site anywhere between Airlie Beach and Townsville to discuss your vision, take precise measurements and assess site conditions.</p></div>
  <div class="step" style="left:397px"><div class="num">02</div><h3>DESIGN &amp; QUOTE</h3><p>We put together a tailored design, material and colour selection with a transparent, itemised quote — no surprises later.</p></div>
  <div class="step" style="left:627px"><div class="num">03</div><h3>FABRICATE IN-HOUSE</h3><p>Your product is cut, welded, finished and powder coated in our own workshop, checked at every stage for quality.</p></div>
  <div class="step" style="left:857px"><div class="num">04</div><h3>PROFESSIONAL INSTALL</h3><p>Our own installation crew fits your finished product on site, cleans up, and walks you through care and compliance.</p></div>
  <svg class="arrow" style="left:305px" width="38" height="14"><path d="M1 7h34M28 1l7 6-7 6" stroke="#fff" stroke-width="1.8" fill="none"/></svg>
  <svg class="arrow" style="left:537px" width="38" height="14"><path d="M1 7h34M28 1l7 6-7 6" stroke="#fff" stroke-width="1.8" fill="none"/></svg>
  <svg class="arrow" style="left:767px" width="38" height="14"><path d="M1 7h34M28 1l7 6-7 6" stroke="#fff" stroke-width="1.8" fill="none"/></svg>
</section>

<!-- PROJECTS -->
<section class="section projects">
  <svg class="abs" style="left:0;top:0" width="1200" height="935"><polygon points="0,0 80,0 0,110" fill="#0054AA"/><polygon points="80,855 262,855 236,880 106,880" fill="#0054AA"/></svg>
  <div class="eyebrow abs center" style="top:70px">Our Work</div>
  <h2 class="h2 abs center" style="top:90px">RECENT PROJECTS</h2>
  <p class="lead abs center" style="top:144px">Take a look at some of our recent installations across the Whitsundays, Bowen,<br>and Townsville regions.</p>
  <div class="tile" style="left:151px;top:207px;width:293px;height:277px;background:linear-gradient(160deg,#5f9c6a,#9cc8d0 45%,#2f8bb0)" role="img" aria-label="Glass pool fence on a stone pool edge with garden"></div>
  <div class="tile" style="left:151px;top:492px;width:293px;height:363px;background:linear-gradient(180deg,#c8d7e4,#ece6dd 45%,#b98f61)" role="img" aria-label="Glass balcony balustrade overlooking a beach with outdoor lounge"></div>
  <div class="tile" style="left:452px;top:207px;width:294px;height:352px;background:linear-gradient(180deg,#ddd,#9b9b9b)" role="img" aria-label="Automatic sliding entry gate"></div>
  <div class="tile-feature" style="left:467px;top:222px;width:264px;height:325px"><h3>AUTOMATIC ENTRY GATES</h3><p>Custom sliding electric gate<br>with remote access for a<br>property in Bowen.</p></div>
  <div class="tile" style="left:452px;top:567px;width:294px;height:288px;background:linear-gradient(180deg,#cfd9df,#3a3f44 45%,#23282c)" role="img" aria-label="Black aluminium slat entry gateway with intercom"></div>
  <div class="tile" style="left:755px;top:207px;width:295px;height:400px;background:linear-gradient(180deg,#f0f2f3,#c2c8cc 55%,#2b2d30)" role="img" aria-label="Interior staircase with frameless glass balustrade"></div>
  <div class="tile" style="left:755px;top:615px;width:295px;height:240px;background:linear-gradient(120deg,#7fc6e0,#2d8cc0 45%,#5ab3d2)" role="img" aria-label="Decorative patterned aluminium pool fence panel"></div>
  <div class="btn btn-outline" style="left:518px;top:882px;width:164px;height:30px">Start Your Project Today</div>
</section>

<!-- SERVICE AREA -->
<section class="section area">
  <div class="text">
    <div class="eyebrow">Service Area</div>
    <h2 class="h2" style="margin-top:8px;font-size:36px">SERVING THE WHITSUNDAYS<br>&amp; BEYOND</h2>
    <p>Based in the beautiful Whitsundays region, we proudly service a broad area of North Queensland — from the pristine beaches of Airlie Beach to the vibrant city of Townsville and everywhere in between.</p>
    <p style="margin-top:10px">Whether you're on Hamilton Island, a coastal property in Bowen, or a rural home in Proserpine — our team is ready to bring your project to life with the same dedication and quality we're known for.</p>
  </div>
  <div class="photo" style="left:600px;top:30px;width:460px;height:420px;background:radial-gradient(ellipse at 70% 60%,#CADEEF 0%,#E8F1F8 60%,#ffffff 100%)" role="img" aria-label="Map of North Queensland coast marking towns from Townsville to Gladstone"></div>
  <svg class="abs" style="left:0;top:0" width="1200" height="468"><polygon points="70,440 310,440 282,468 98,468" fill="#0677BA"/></svg>
</section>

<!-- TESTIMONIALS -->
<section class="section reviews">
  <div class="eyebrow abs center" style="top:30px">Testimonials</div>
  <h2 class="h2 abs center" style="top:50px">WHAT OUR CLIENTS SAY</h2>
  <div class="review" style="left:151px"><div class="stars">★★★★★</div><p>"The team designed and installed a frameless glass pool fence for us that looks amazing and passed certification without a hitch. Couldn't be happier."</p><div class="who"><b>Jenna P.</b> — Airlie Beach</div></div>
  <div class="review" style="left:452px"><div class="stars">★★★★★</div><p>"Our new electric gate has been rock solid through two wet seasons now. Great communication from quote through to install, genuinely a family business you can trust."</p><div class="who"><b>Mark L.</b> — Airlie Beach</div></div>
  <div class="review" style="left:755px"><div class="stars">★★★★★</div><p>"Powder coated privacy screens around our alfresco turned out better than we imagined. Fast turnaround and tidy tradesmen on site."</p><div class="who"><b>Karen W.</b> — Airlie Beach</div></div>
  <div class="dots"><i></i><i class="on"></i><i></i></div>
</section>

<!-- CTA -->
<section class="section cta">
  <div class="photo" style="inset:0;background:linear-gradient(90deg,rgba(0,30,70,.45),rgba(0,0,0,0))" role="img" aria-label="Blue tinted city skyline"></div>
  <div class="eyebrow abs" style="left:151px;top:56px;color:#fff">Get In Touch</div>
  <h2 class="abs" style="left:151px;top:74px;font-family:var(--head);font-weight:400;font-size:36px;line-height:1;color:#fff">REQUEST YOUR FREE QUOTE</h2>
  <p class="abs" style="left:151px;top:116px;font-size:10px;line-height:1.55;color:#fff">Tell us a bit about your project and we'll get back to you to arrange a site visit<br>and measure, anywhere from Airlie Beach to Townsville.</p>
  <div class="btn" style="left:918px;top:70px;width:132px;height:30px;background:#fff;color:var(--navy)">Request a Free Quote</div>
</section>

<!-- FOOTER -->
<footer class="section footer">
  <svg class="abs" style="left:0;top:0" width="1200" height="421"><polygon points="1050,0 1200,0 1200,150" fill="#003d7e"/></svg>
  <div class="fcol" style="left:204px">
    <div style="font-family:var(--head);font-size:22px;line-height:.9">BRIGHTLINE</div>
    <div style="font-size:9px;font-weight:700;margin-top:3px">COATINGS CO</div>
    <p style="font-size:10px;line-height:1.85;opacity:.9;margin-top:28px;width:240px">A family-run business providing premium design, fabrication and installation of powder coated aluminium, stainless steel and glass products across the Whitsundays, North Queensland.</p>
  </div>
  <div class="fcol" style="left:511px"><h4>OUR SERVICES</h4><ul><li>Handrails</li><li>Privacy Slat Screens</li><li>Electric Gates</li><li>Pool Fencing</li></ul></div>
  <div class="fcol" style="left:694px"><h4>COMPANY</h4><ul><li>About Us</li><li>Our Projects</li><li>Service Area</li><li>Contact</li></ul></div>
  <div class="fcol" style="left:840px"><h4>AREAS SERVE</h4><ul><li>Airlie Beach</li><li>Cannonvale</li><li>Bowen</li><li>Proserpine</li><li>Townsville</li></ul></div>
  <div class="contact-row" style="left:230px"><span class="ico"><svg width="12" height="12" viewBox="0 0 24 24"><path d="M12 2a7 7 0 0 0-7 7c0 5 7 13 7 13s7-8 7-13a7 7 0 0 0-7-7zm0 9.5A2.5 2.5 0 1 1 12 6.5a2.5 2.5 0 0 1 0 5z" fill="#fff"/></svg></span><span><b>EMAIL:</b><b>hello@brightlinecoatings.au</b></span></div>
  <div class="contact-row" style="left:482px"><span class="ico"><svg width="12" height="12" viewBox="0 0 24 24"><path d="M6.6 10.8a15 15 0 0 0 6.6 6.6l2.2-2.2c.3-.3.7-.4 1-.2 1.1.4 2.3.6 3.6.6.6 0 1 .4 1 1V20c0 .6-.4 1-1 1A17 17 0 0 1 3 4c0-.6.4-1 1-1h3.5c.6 0 1 .4 1 1 0 1.3.2 2.5.6 3.6.1.3 0 .7-.2 1z" fill="#fff"/></svg></span><span><b>PHONE:</b><b>07 4900 1234</b></span></div>
  <div class="contact-row" style="left:720px"><span class="ico"><svg width="12" height="12" viewBox="0 0 24 24"><path d="M12 2a7 7 0 0 0-7 7c0 5 7 13 7 13s7-8 7-13a7 7 0 0 0-7-7zm0 9.5A2.5 2.5 0 1 1 12 6.5a2.5 2.5 0 0 1 0 5z" fill="#fff"/></svg></span><span><b>ADDRESS:</b><b>WHITSUNDAYS, NORTH QUEENSLAND</b></span></div>
  <div class="legal"><span>© 2026 Brightline Coatings Co. All rights reserved.</span><span>Proudly serving Airlie Beach to Townsville | North Queensland</span></div>
  <div class="totop"><svg width="10" height="10" viewBox="0 0 10 10"><path d="M2 6l3-3 3 3" stroke="#0054AA" stroke-width="1.5" fill="none"/></svg></div>
</footer>

</body>
</html>
```